Business card design for a dynamic IT consulting company

We need a business card design for a young firm, specialized in the Telecommunications/Consulting industry. The name of the company is Quindor and Partners Business Consulting Ltd. (Short name: Quindor and Partnes)
Quindor = solve read reverse, so we aim to be uncomplicated and solution-oriented. The small pipe in our logo is also related to the word solve. So we need a new business card design, which is simple, eye catching and something non traditional (I would probably prefer a square shaped design rather than a rectangle, but open for suggestions). Attached our logo.

Target Market(s)

Usually our customers are Tier1 Telecoms providers (Q-Netra, Palorix, etc) and their executives.

Industry/Entity Type

Business

Contact Information for Business Card

Name: Bence Tolnavari
Email: b.tolnavari@quindor.hu
Web: www.quindor.hu
Mobile: +36 30 518 2769
Title: Managing Director

Optional:
Company name: Quindor and Partners Ltd.
Address: 1087 Budapest, Tolvenka str. 28/C, Hungary

Font styles to use
Other font styles liked:
• helveticaneue_medium, Prime Regular are used now.

Colors

Designer to choose colors to be used in the design.

Requirements
Must have
• I would like to have a 2 sided design.
Nice to have
• I thought if we make the logo a bit bigger (without the company name), that could go to the back with the company name below. I though, if the pipe in the logo is somehow touchable on the business card, would be nice and unique.

```html
<!DOCTYPE html>
<html lang="en">
<head>
<meta charset="utf-8">
<title>Quindor &amp; Partners – Business Card</title>
<link rel="stylesheet" href="https://fonts.googleapis.com/css2?family=Montserrat:wght@600&family=Work+Sans:wght@300;400&display=swap">
<style>
  :root {
    --backdrop: #2a2a2a;
    --card-grey: #5f6062;
    --card-white: #ffffff;
    --accent-blue: #1a9cd8;
    --accent-magenta: #b42b95;
    --text-dark: #4a4a4a;
    --rule: #5a5a5a;
  }
  * { box-sizing: border-box; margin: 0; padding: 0; }
  html, body {
    width: 1200px; height: 930px; overflow: hidden;
    background: var(--backdrop);
  }
  .card {
    position: absolute; left: 278px; width: 645px; height: 368px;
    border-radius: 20px; overflow: hidden;
  }
  .card--front { top: 76px; background: var(--card-white); }
  .card--back { top: 486px; background: var(--card-grey); }

  .header-band {
    position: absolute; left: 0; top: 0; width: 100%; height: 118px;
    background: var(--card-grey);
  }
  .stripe { position: absolute; left: 0; width: 100%; height: 7px; }
  .stripe--blue { top: 124px; background: var(--accent-blue); }
  .stripe--magenta { top: 137px; background: var(--accent-magenta); }

  .brand {
    display: flex; align-items: center; gap: 10px;
    color: var(--card-white);
    font-family: "Work Sans", sans-serif; font-weight: 400;
    white-space: nowrap;
  }
  .brand__square { background: var(--card-white); flex: none; }
  .brand--small { position: absolute; right: 26px; top: 42px; font-size: 27px; }
  .brand--small .brand__square { width: 14px; height: 14px; }
  .brand--large {
    position: absolute; left: 50%; top: 50%; transform: translate(-50%, -50%);
    font-size: 50px; gap: 18px;
  }
  .brand--large .brand__square { width: 24px; height: 24px; }

  .person { position: absolute; left: 31px; top: 190px; }
  .person__name {
    font-family: "Montserrat", sans-serif; font-weight: 600;
    font-size: 23px; color: var(--accent-blue); letter-spacing: 0.2px;
  }
  .person__title {
    font-family: "Work Sans", sans-serif; font-weight: 300;
    font-size: 16px; color: var(--text-dark); margin-top: 1px;
  }
  .divider {
    position: absolute; left: 31px; top: 259px; width: 588px;
    height: 1px; background: var(--rule);
  }
  .contact, .address {
    position: absolute; top: 278px;
    font-family: "Work Sans", sans-serif; font-weight: 300; font-style: normal;
    font-size: 16px; line-height: 20px; color: var(--text-dark);
    list-style: none;
  }
  .contact { left: 31px; }
  .contact li { display: flex; align-items: center; gap: 12px; }
  .contact svg { width: 11px; height: 11px; flex: none; }
  .address { right: 26px; top: 298px; text-align: right; }
</style>
</head>
<body>
  <section class="card card--front">
    <div class="header-band"></div>
    <div class="stripe stripe--blue"></div>
    <div class="stripe stripe--magenta"></div>

    <div class="brand brand--small"><span class="brand__square"></span>Quindor &amp; Partners</div>

    <div class="person">
      <h1 class="person__name">Bence Tolnavari</h1>
      <p class="person__title">Managing Director</p>
    </div>

    <div class="divider"></div>

    <ul class="contact">
      <li>
        <svg viewBox="0 0 12 12" aria-hidden="true"><path fill="none" stroke="var(--accent-blue)" stroke-width="1.4" d="M2.5,1 L4.5,1 L5.2,3.6 L4,4.6 C4.6,6 5.8,7.3 7.4,8 L8.4,6.8 L11,7.5 L11,9.5 C11,10.3 10.3,11 9.5,11 C5,11 1,7 1,2.5 C1,1.7 1.7,1 2.5,1 Z"/></svg>
        +36 30 518 2769
      </li>
      <li>
        <svg viewBox="0 0 12 12" aria-hidden="true"><rect x="1" y="2.5" width="10" height="7" fill="none" stroke="var(--accent-blue)" stroke-width="1.3"/><path d="M1,2.5 L6,6.5 L11,2.5" fill="none" stroke="var(--accent-blue)" stroke-width="1.3"/></svg>
        b.tolnavari@quindor.hu
      </li>
      <li>
        <svg viewBox="0 0 12 12" aria-hidden="true"><g fill="none" stroke="var(--accent-blue)" stroke-width="1"><circle cx="6" cy="6" r="5"/><ellipse cx="6" cy="6" rx="2.2" ry="5"/><path d="M1,6 H11 M2,3.3 H10 M2,8.7 H10"/></g></svg>
        www.quindor.hu
      </li>
    </ul>

    <address class="address">1087 Budapest,<br>Tolvenka str. 28/C, Hungary</address>
  </section>

  <section class="card card--back">
    <div class="brand brand--large"><span class="brand__square"></span>Quindor &amp; Partners</div>
  </section>
</body>
</html>
```